Shopping center investment profile

We need to design a two-page 8.5" x 11" brochure that can be used as a template for profiling our shopping centers and demonstrating our track record to investors.

Our company (QLM Real Estate Investments) owns retail shopping centers in the southwestern United States. Our website is www.qlmvx.example, but we will be redesigning and modernizing the website and logo in the near future, so please do not use the color schemes or framework of the website for the brochure.

Our investors are institutional and high net worth investors who typically have an existing relationship with our company. They are determining whether to invest multi-millions of dollars in a shopping center opportunity, so the brochure needs to be professional, very high quality and provide key information about the specific property.
Updates

Additional guidance on color scheme:

We would like to see a Blue (something like Hex #5A61BC) and Gold (Hex #EDB215) or (Hex #DDA24B) color scheme with some Black accents 

Thank you!

Target Market(s)

Our target audiences are institutional investors, high net-worth individuals, financial firms and medium to large commercial real estate companies.

Industry/Entity Type

Investment

Requirements
Must have
• Clean and modern look with corresponding fonts and colors.
• Incorporates the information found in the attached "Harborline Commons profile" Pages or PDF file.
• Final file design files that can be modified easily
Nice to have
• Two examples of industry brochures are attached. These are examples of the professional quality that we are looking for, not necessarily the design or format.

```html
<!DOCTYPE html>
<html lang="en">
<head>
<meta charset="utf-8">
<title>Harborline Commons – Property Profile</title>
<link href="https://fonts.googleapis.com/css2?family=Roboto+Condensed:wght@700&family=Arimo:wght@400;700&display=swap" rel="stylesheet">
<style>
  :root{
    --brand-blue:#5a61bc;
    --brand-gold:#edb215;
    --ink:#1e1d22;
    --sky-deep:#2d6ac4;
    --sky-light:#9dbbe0;
    --facade:#c9976f;
    --asphalt:#5e5e63;
    --text-light:#e8e7ea;
    --white:#ffffff;
  }
  *{margin:0;padding:0;box-sizing:border-box}
  html,body{width:931px;height:1200px;overflow:hidden;background:var(--ink)}
  .page{position:relative;width:931px;height:1200px;font-family:"Arimo",Arial,sans-serif;color:var(--text-light);background:var(--ink)}
  .hero{position:absolute;left:0;top:0;width:931px;height:688px;
    background:linear-gradient(180deg,var(--sky-deep) 0%,#4d86d0 22%,var(--sky-light) 42%,var(--facade) 56%,#a0705a 72%,var(--asphalt) 84%,#4a4a4f 100%)}
  .hero-rule{position:absolute;left:0;top:684px;width:931px;height:4px;background:var(--brand-gold)}
  .masthead{position:absolute;left:56px;top:74px}
  .property-name{font-family:"Roboto Condensed","Arial Narrow",sans-serif;font-weight:700;font-size:66px;line-height:1;color:var(--white);letter-spacing:-.5px}
  .location{font-family:"Roboto Condensed","Arial Narrow",sans-serif;font-weight:700;font-size:31px;color:var(--white);margin-top:12px;line-height:1}
  .doc-type{font-family:"Roboto Condensed","Arial Narrow",sans-serif;font-weight:700;font-size:31px;color:var(--brand-gold);margin-top:11px;line-height:1}
  .section-title{font-family:"Roboto Condensed","Arial Narrow",sans-serif;font-weight:700;font-size:26px;color:var(--brand-gold);line-height:1}
  .summary{position:absolute;left:55px;top:719px;width:385px}
  .summary .section-title{margin-bottom:20px;margin-left:6px}
  .facts{width:100%;border-collapse:collapse;font-size:14.5px}
  .facts td{padding:4px 6px;line-height:18px;border-bottom:1px solid var(--brand-blue)}
  .facts td.value{text-align:right}
  .opportunity{position:absolute;left:482px;top:719px;width:425px}
  .results{position:absolute;left:482px;top:980px;width:425px}
  .section-title + .bullets{margin-top:20px}
  .bullets{list-style:none;font-size:14.5px;line-height:18.4px}
  .bullets li{position:relative;padding-left:17px}
  .bullets li::before{content:"";position:absolute;left:0;top:5px;width:9px;height:9px;border-radius:50%;background:var(--brand-gold)}
  .brand{position:absolute;left:56px;top:1068px;color:var(--white);font-family:"Arimo",Arial,sans-serif;font-weight:400}
  .brand-mark{font-size:72px;line-height:1;letter-spacing:-1px}
  .brand-sub{font-size:22px;line-height:1;margin-top:6px}
</style>
</head>
<body>
<div class="page">
  <div class="hero" role="img" aria-label="Rendering of the shopping center storefronts with trees, parked cars and shoppers under a blue sky"></div>
  <div class="hero-rule"></div>

  <header class="masthead">
    <h1 class="property-name">Harborline Commons</h1>
    <p class="location">Gilbert, Arizona</p>
    <p class="doc-type">Property Profile</p>
  </header>

  <section class="summary">
    <h2 class="section-title">Summary</h2>
    <table class="facts">
      <tr><td>Property Type</td><td class="value">Shopping Center</td></tr>
      <tr><td>Size</td><td class="value">79,490 sq ft</td></tr>
      <tr><td>Acquisition Date</td><td class="value">April 2011</td></tr>
      <tr><td>Total Investment</td><td class="value">$X,XXX,XXX</td></tr>
      <tr><td>Purchase Occupancy</td><td class="value">8.39%</td></tr>
      <tr><td>Current Occupancy</td><td class="value">97.29%</td></tr>
      <tr><td>Projected 5-year IRR (Unleveraged)</td><td class="value">XX.XX%</td></tr>
    </table>
  </section>

  <section class="opportunity">
    <h2 class="section-title">Opportunity</h2>
    <ul class="bullets">
      <li>Bank owned property with attractive purchase price</li>
      <li>Strong relationship with seller’s broker and decision makers</li>
      <li>Redevelopment upside with management and leasing</li>
      <li>No major renovations required</li>
      <li>Gilbert location has very strong population, education<br>and income demographics</li>
      <li>Adjacent to premier 2,500-residence master planned<br>community of Sunmesa Lakes</li>
      <li>Strong employment area with the new Crestview Gateway<br>hospital and the adjacent Larkspur Oncology center</li>
    </ul>
  </section>

  <section class="results">
    <h2 class="section-title">Results</h2>
    <ul class="bullets">
      <li>Stabilized the shopping center within three years,<br>producing excellent results for investors</li>
      <li>Transformed the center into a vibrant destination that<br>the surrounding community is excited about</li>
      <li>Transitioned legacy tenants to upgrade the business operators</li>
      <li>Reduced the shopping center’s operating expenses<br>by replacing vendors and appealing property taxes</li>
    </ul>
  </section>

  <div class="brand">
    <div class="brand-mark">QLM</div>
    <div class="brand-sub">REAL ESTATE</div>
  </div>
</div>
</body>
</html>
```